Redesign and move to Wordpress for corvandel.com

Our website needs a redesign and at the same time we are moving it to Wordpress. Please help us with a new digital professional look and feel.

We are an Australian Software Engineering company specialising in advanced software development using in A.I., PLatform Engineering, Integration and Cloud. See the current corvandel.com for more information about us.

```html
<!DOCTYPE html>
<html lang="en">
<head>
<meta charset="utf-8">
<title>Corvandel — Reliable Smart Software Engineering</title>
<link href="https://fonts.googleapis.com/css2?family=Orbitron:wght@400;500;600&family=Montserrat:wght@400;500;600&display=swap" rel="stylesheet">
<style>
:root{
  --bg:#0a1a2f;
  --nav:#0b1628;
  --card:#0c213b;
  --card-line:#163556;
  --blue:#1a86d4;
  --blue-bright:#2a9be8;
  --white:#ffffff;
  --muted:#b9c6d6;
  --dim:#4e6480;
  --display:'Orbitron', sans-serif;
  --body:'Montserrat', sans-serif;
}
*{box-sizing:border-box;margin:0;padding:0}
html,body{width:1200px;height:4138px;overflow:hidden}
body{background:var(--bg);color:var(--white);font-family:var(--body);position:relative}
.display{font-family:var(--display);font-weight:500;letter-spacing:1px}

/* nav */
.site-nav{position:absolute;left:0;top:0;width:1200px;height:84px;background:var(--nav)}
.brand{position:absolute;font-family:var(--display);font-weight:400;color:var(--white);letter-spacing:1px}
.nav-brand{left:103px;top:26px;font-size:28px}
.nav-links{position:absolute;top:36px;left:377px;font-family:var(--display);font-size:14px}
.nav-links a{color:var(--white);text-decoration:none;position:absolute;white-space:nowrap}
.nav-links a.active{color:var(--blue-bright)}
.search{position:absolute;left:916px;top:24px;width:181px;height:43px;border:1px solid var(--muted);display:flex;justify-content:flex-end}
.search span{width:43px;height:41px;background:var(--blue);display:flex;align-items:center;justify-content:center}

/* hero */
.hero{position:absolute;left:0;top:84px;width:1200px;height:599px;background:radial-gradient(circle at 890px 250px,#f3e3d0 0,#c98c6a 40px,#2b5f8f 140px,#123a66 320px,#081a33 620px)}
.hero-title{position:absolute;left:82px;top:275px;font-size:41px;line-height:46px}
.hero-text{position:absolute;left:85px;top:376px;font-size:15px;line-height:28px;font-weight:500;width:450px}
.btn{position:absolute;background:var(--blue);color:var(--white);font-family:var(--display);font-weight:500;display:flex;align-items:center;justify-content:center;clip-path:polygon(6% 0,100% 0,94% 100%,0 100%)}
.hero-btn{left:88px;top:443px;width:166px;height:39px;font-size:15px}

.section-title{position:absolute;left:0;width:1200px;text-align:center;font-size:32px}

/* services */
.svc-card{position:absolute;top:880px;width:238px;height:338px;background:var(--card);border:1px solid var(--card-line);border-radius:12px;text-align:center}
.svc-card.featured{background:var(--blue);border-color:var(--blue)}
.svc-icon{position:absolute;left:69px;top:31px;width:100px;height:100px;border-radius:50%;background:#173c66;display:flex;align-items:center;justify-content:center}
.featured .svc-icon{background:transparent;border:2px solid var(--white)}
.svc-name{position:absolute;left:24px;width:190px;font-family:var(--display);font-weight:500;font-size:18px;line-height:23px;letter-spacing:.5px}
.svc-desc{position:absolute;left:14px;width:210px;top:224px;font-size:12px;line-height:21px;color:#e1e8f0}
.car-arrow{position:absolute;width:33px;height:24px;background:var(--blue);font-size:12px;display:flex;align-items:center;justify-content:center;clip-path:polygon(12% 0,100% 0,88% 100%,0 100%)}

/* about */
.about-back{position:absolute;left:193px;top:1327px;width:358px;height:333px;background:var(--blue);border-radius:14px}
.about-img{position:absolute;left:125px;top:1346px;width:407px;height:383px;border-radius:16px;background:linear-gradient(135deg,#1f4d7c,#0b1e36 55%,#04080f)}
.about-title{position:absolute;left:638px;top:1338px;font-size:32px}
.about-text{position:absolute;left:638px;top:1382px;width:460px;font-size:15px;line-height:26px;color:#e6edf5}
.about-text p+p{margin-top:10px}
.about-btn{left:641px;top:1647px;width:165px;height:40px;font-size:16px}

/* clients */
.client-band{position:absolute;left:103px;top:1892px;width:999px;height:103px;display:flex;background:#0c1f37}
.client{flex:1;display:flex;align-items:center;justify-content:center;font-weight:600;font-size:30px;color:var(--white);border:1px solid #102a48}
.client.active{border:2px solid #1f4f86}
.client i{display:inline-block;width:16px;height:16px;background:var(--white);margin-right:10px}

/* news */
.news-title{position:absolute;left:103px;top:2228px;font-size:32px}
.news-arrows{position:absolute;left:988px;top:2225px;display:flex;gap:6px}
.news-arrows span{width:50px;height:40px;display:flex;align-items:center;justify-content:center;background:#0f2a4a;clip-path:polygon(12% 0,100% 0,88% 100%,0 100%);font-size:16px}
.news-arrows span.on{background:var(--blue)}
.news-card{position:absolute;top:2313px;width:482px;height:468px;background:#0d2440;border-radius:10px;overflow:hidden}
.news-img{width:482px;height:275px}
.news-card h3{position:absolute;left:32px;top:307px;font-family:var(--display);font-weight:500;font-size:20px;letter-spacing:1px}
.news-card p{position:absolute;left:35px;top:345px;width:420px;font-size:13px;line-height:24px;color:#d5deea}
.news-card a{position:absolute;left:36px;top:424px;font-family:var(--display);font-size:15px;color:var(--blue-bright)}

/* booking */
.book-title{position:absolute;left:0;top:2990px;width:1200px;text-align:center;font-size:33px;line-height:42px}
.booking{position:absolute;left:198px;top:3118px;width:804px;height:333px;background:#0f2745;border-radius:8px}
.host{position:absolute;left:16px;top:16px;width:403px;height:296px;background:#0b1c33;border-radius:8px;text-align:center}
.avatar{position:absolute;left:163px;top:51px;width:76px;height:76px;border-radius:50%;background:linear-gradient(#5b6f86,#2a3646);border:2px solid #dfe6ee}
.host p{position:absolute;left:0;width:403px;font-family:var(--display);font-size:16px}
.calendar{position:absolute;left:456px;top:30px;width:320px}
.month{position:absolute;left:0;width:320px;text-align:center;top:0;font-size:16px;font-weight:600}
.day{position:absolute;width:40px;text-align:center;font-size:10px}
.wk{font-weight:600}
.day.off{color:var(--dim)}
.day.sel{width:36px;height:36px;border-radius:50%;background:var(--white);color:#0b1c33;line-height:36px;margin-left:2px;margin-top:-11px;font-weight:600}

/* newsletter */
.newsletter{position:absolute;left:0;top:3545px;width:1200px;height:269px;background:var(--blue)}
.newsletter h2{position:absolute;left:0;top:45px;width:1200px;text-align:center;font-family:var(--display);font-weight:500;font-size:25px;line-height:35px;letter-spacing:1px}
.email-field{position:absolute;left:300px;top:146px;width:455px;height:41px;border:1px solid #c5e2f6;border-radius:4px;font-family:var(--display);font-size:15px;padding:11px 28px;clip-path:polygon(1.5% 0,100% 0,98.5% 100%,0 100%)}
.submit{position:absolute;left:765px;top:146px;width:131px;height:41px;background:#0b1628;font-family:var(--display);font-size:15px;display:flex;align-items:center;justify-content:center;clip-path:polygon(8% 0,100% 0,92% 100%,0 100%)}

/* footer */
.foot-brand{left:103px;top:3917px;font-size:46px}
.foot-links a{position:absolute;top:3900px;font-family:var(--display);font-size:16px;color:var(--white);text-decoration:none}
.contact{position:absolute;top:3955px;display:flex;gap:12px}
.contact .ic{width:38px;height:38px;border-radius:50%;background:var(--blue);display:flex;align-items:center;justify-content:center}
.contact b{display:block;font-family:var(--display);font-weight:500;font-size:16px;color:var(--blue-bright)}
.contact span{display:block;font-size:12px;line-height:19px;margin-top:2px}
.rule{position:absolute;left:103px;top:4051px;width:994px;height:1px;background:#53657c}
.copyright{position:absolute;left:0;top:4081px;width:1200px;text-align:center;font-family:var(--display);font-size:15px}
</style>
</head>
<body>

<header class="site-nav">
  <div class="brand nav-brand">corvandel</div>
  <nav class="nav-links">
    <a class="active" style="left:0">Home</a>
    <a style="left:95px">Our Services</a>
    <a style="left:247px">About Us</a>
    <a style="left:367px">Blog</a>
    <a style="left:445px">Contact</a>
  </nav>
  <div class="search"><span><svg width="18" height="18" viewBox="0 0 18 18" fill="none" stroke="#fff" stroke-width="2.4"><circle cx="7.5" cy="7.5" r="5.5"/><path d="M12 12l5 5"/></svg></span></div>
</header>

<section class="hero" role="img" aria-label="Robotic hand and human hand reaching toward a glowing light bulb over a blue circuit-board backdrop"></section>
<h1 class="hero-title display">Reliable Smart<br>Software Engineering</h1>
<p class="hero-text">We have been on a mission to make complex custom enterprise integration accessible to any organisation.</p>
<div class="btn hero-btn">Get Started</div>

<h2 class="section-title display" style="top:783px">Our Services</h2>
<div class="car-arrow" style="left:32px;top:1036px">«</div>
<div class="car-arrow" style="left:1144px;top:1036px">»</div>

<article class="svc-card" style="left:95px">
  <div class="svc-icon"><svg width="54" height="54" viewBox="0 0 54 54" fill="none" stroke="#2a9be8" stroke-width="2"><rect x="5" y="6" width="44" height="34" rx="2"/><path d="M14 34V24M22 34V18M30 34V26M38 34V14"/><path d="M20 48h14M27 40v8"/></svg></div>
  <div class="svc-name" style="top:147px">ENTERPRISE<br>Systems<br>Integration</div>
  <p class="svc-desc">Automate your business processes internally or externally to improve data quality and process efficiency</p>
</article>
<article class="svc-card" style="left:352px">
  <div class="svc-icon"><svg width="60" height="60" viewBox="0 0 60 60" fill="none" stroke="#2a9be8" stroke-width="2"><circle cx="30" cy="30" r="8"/><circle cx="30" cy="8" r="4"/><circle cx="30" cy="52" r="4"/><circle cx="8" cy="30" r="4"/><circle cx="52" cy="30" r="4"/><circle cx="14" cy="14" r="3"/><circle cx="46" cy="46" r="3"/><circle cx="46" cy="14" r="3"/><circle cx="14" cy="46" r="3"/><path d="M30 12v10M30 38v10M12 30h10M38 30h10M16 16l8 8M44 44l-8-8M44 16l-8 8M16 44l8-8"/></svg></div>
  <div class="svc-name" style="top:170px">Microservices</div>
  <p class="svc-desc">Leverage Microservices Architecture to enable quick deployment, dynamically scalable service performance, team</p>
</article>
<article class="svc-card featured" style="left:610px">
  <div class="svc-icon"><svg width="58" height="58" viewBox="0 0 58 58" fill="none" stroke="#fff" stroke-width="2"><rect x="10" y="18" width="38" height="26" rx="2"/><circle cx="29" cy="31" r="7"/><path d="M6 48h46M18 18V8M29 18V6M40 18V8"/><circle cx="18" cy="6" r="2"/><circle cx="40" cy="6" r="2"/></svg></div>
  <div class="svc-name" style="top:151px">PLatform<br>Engineering</div>
  <p class="svc-desc">For organisations looking to manage the security and cost risks around their cloud infrastructure management for applications</p>
</article>
<article class="svc-card" style="left:867px">
  <div class="svc-icon"><svg width="56" height="56" viewBox="0 0 56 56" fill="none" stroke="#2a9be8" stroke-width="2"><rect x="12" y="12" width="32" height="32" rx="3"/><path d="M20 12V4M28 12V4M36 12V4M20 44v8M28 44v8M36 44v8M12 20H4M12 28H4M12 36H4M44 20h8M44 28h8M44 36h8"/><text x="28" y="34" text-anchor="middle" font-family="Montserrat, sans-serif" font-size="14" fill="#2a9be8" stroke="none">AI</text></svg></div>
  <div class="svc-name" style="top:154px;left:4px;width:230px">Conversational<br>AI</div>
  <p class="svc-desc">Enabling legacy systems with conversational user interfaces, or simply building intelligent natural language based services,</p>
</article>

<div class="about-back"></div>
<div class="about-img" role="img" aria-label="Presenter speaking in front of a large AI technology display screen"></div>
<h2 class="about-title display">About Corvandel</h2>
<div class="about-text">
  <p>Since our inception in 2013, we have been on a mission to make complex custom enterprise integration accessible to any organization, regardless of industry, size, or location.</p>
  <p>At Corvandel, we craft bespoke software solutions that are not available on the market. By building organizations market-leading products, process automation, legacy system enablement, or advanced intelligent systems, we empower our customers to achieve a competitive edge in their industry.</p>
</div>
<div class="btn about-btn">Read More</div>

<h2 class="section-title display" style="top:1815px">Our Clients</h2>
<div class="client-band">
  <div class="client">Halvern</div>
  <div class="client"><i></i>Tessaro</div>
  <div class="client active">Korrick</div>
  <div class="client">Brightwell</div>
</div>

<h2 class="news-title display">News &amp; articles</h2>
<div class="news-arrows"><span>«</span><span class="on">»</span></div>
<article class="news-card" style="left:104px">
  <div class="news-img" role="img" aria-label="Hand touching a glowing AI interface on a dark blue background" style="background:linear-gradient(135deg,#0f3a66,#0a2340 60%,#061426)"></div>
  <h3>AI in SOFTWARE ENGINEERING</h3>
  <p>(Codewell Blog) Codewell Pilot is widely known for its code generation feature. Learn how the AI assistant's abilities can extend beyond just code generation.</p>
  <a>Read More</a>
</article>
<article class="news-card" style="left:614px">
  <div class="news-img" role="img" aria-label="Engineering team reviewing a design on a large screen in a bright office" style="background:linear-gradient(135deg,#dfe7ef,#a9bccf 55%,#5b7391)"></div>
  <h3>INDUSTRY RESEARCH</h3>
  <p>(Northgate Research) Large language models (LLMs) have revolutionized various tasks, but prompt engineering remains a challenge. Enter PROMPTA: an open-source tool</p>
  <a>Read More</a>
</article>

<h2 class="book-title display">Book an obligation free consultation<br>with our Lead Technologist</h2>
<div class="booking">
  <div class="host">
    <div class="avatar" role="img" aria-label="Portrait of the CTO"></div>
    <p style="top:165px">Meet with our CTO</p>
    <p style="top:213px">Meeting duration</p>
    <p style="top:245px">30Mins</p>
  </div>
  <div class="calendar">
    <div class="month">‹&nbsp;&nbsp;&nbsp;January 2025&nbsp;&nbsp;&nbsp;›</div>
    <div class="day wk" style="left:1px;top:46px">SUN</div>
    <div class="day wk" style="left:47px;top:46px">MON</div>
    <div class="day wk" style="left:94px;top:46px">TUE</div>
    <div class="day wk" style="left:139px;top:46px">WED</div>
    <div class="day wk" style="left:185px;top:46px">THU</div>
    <div class="day wk" style="left:232px;top:46px">FRI</div>
    <div class="day wk" style="left:277px;top:46px">SAT</div>

    <div class="day off" style="left:139px;top:86px">1</div>
    <div class="day off" style="left:185px;top:86px">2</div>
    <div class="day off" style="left:232px;top:86px">3</div>
    <div class="day off" style="left:277px;top:86px">4</div>

    <div class="day off" style="left:1px;top:127px">5</div>
    <div class="day off" style="left:47px;top:127px">6</div>
    <div class="day off" style="left:94px;top:127px">7</div>
    <div class="day off" style="left:139px;top:127px">8</div>
    <div class="day off" style="left:185px;top:127px">9</div>
    <div class="day off" style="left:232px;top:127px">10</div>
    <div class="day off" style="left:277px;top:127px">11</div>

    <div class="day off" style="left:1px;top:169px">12</div>
    <div class="day off" style="left:47px;top:169px">13</div>
    <div class="day off" style="left:94px;top:169px">14</div>
    <div class="day sel" style="left:137px;top:169px">15</div>
    <div class="day" style="left:185px;top:169px">16</div>
    <div class="day" style="left:232px;top:169px">17</div>
    <div class="day off" style="left:277px;top:169px">18</div>

    <div class="day off" style="left:1px;top:211px">19</div>
    <div class="day off" style="left:47px;top:211px">20</div>
    <div class="day off" style="left:94px;top:211px">21</div>
    <div class="day" style="left:139px;top:211px">22</div>
    <div class="day" style="left:185px;top:211px">23</div>
    <div class="day" style="left:232px;top:211px">24</div>
    <div class="day off" style="left:277px;top:211px">25</div>

    <div class="day off" style="left:1px;top:251px">26</div>
    <div class="day off" style="left:47px;top:251px">27</div>
    <div class="day off" style="left:94px;top:251px">28</div>
    <div class="day" style="left:139px;top:251px">29</div>
    <div class="day" style="left:185px;top:251px">30</div>
    <div class="day" style="left:232px;top:251px">31</div>
  </div>
</div>

<section class="newsletter">
  <h2>Australia's Largest health charity implements<br>Corvandel API Msg Bus</h2>
  <div class="email-field">Email*</div>
  <div class="submit">Submit</div>
</section>

<footer>
  <div class="brand foot-brand">corvandel</div>
  <nav class="foot-links">
    <a style="left:514px;text-decoration:underline">Home</a>
    <a style="left:622px">Our Services</a>
    <a style="left:792px">About Us</a>
    <a style="left:927px">Blog</a>
    <a style="left:1015px">Contact</a>
  </nav>
  <div class="contact" style="left:534px">
    <div class="ic"><svg width="16" height="20" viewBox="0 0 16 20"><path d="M8 0a8 8 0 0 0-8 8c0 6 8 12 8 12s8-6 8-12a8 8 0 0 0-8-8z" fill="#fff"/><circle cx="8" cy="8" r="3" fill="#1a86d4"/></svg></div>
    <div><b>Location :</b><span>Suite 210, 48 Harbour Lane<br>Melbourne, VIC , 3006</span></div>
  </div>
  <div class="contact" style="left:752px">
    <div class="ic"><svg width="18" height="18" viewBox="0 0 24 24"><path d="M6.6 10.8a15 15 0 0 0 6.6 6.6l2.2-2.2a1 1 0 0 1 1-.25 11 11 0 0 0 3.6.6 1 1 0 0 1 1 1V20a1 1 0 0 1-1 1A17 17 0 0 1 3 4a1 1 0 0 1 1-1h3.5a1 1 0 0 1 1 1 11 11 0 0 0 .6 3.6 1 1 0 0 1-.25 1z" fill="#fff"/></svg></div>
    <div><b>Phone :</b><span>1800 555 019</span></div>
  </div>
  <div class="contact" style="left:938px">
    <div class="ic"><svg width="18" height="14" viewBox="0 0 18 14"><rect width="18" height="14" rx="2" fill="#fff"/><path d="M1 2l8 6 8-6" fill="none" stroke="#1a86d4" stroke-width="1.6"/></svg></div>
    <div><b>Email :</b><span>info@corvandel.com</span></div>
  </div>
  <div class="rule"></div>
  <p class="copyright">©2025 corvandel | All Rights Reserved</p>
</footer>

</body>
</html>
```